Corlani Vaginal Suppositories eCommerce Website Design

We are designing an ecommerce website for a new company and product. The product is vaginal moisturizer suppositories. We are going to develop this site on Shopify so you can add in any featured you have knowledge of in Shopify.

We are purposefully not adding any images to allow you to create something with your style. A similar product is tandelivy.com. We would like a site similar to this in style, but obviously different not to look the same. It is a product for women so it needs to be a very feminine theme. We have had designers use thier own illustrations in previous designs that looked great, or stock images that don't look "stock" would be good. We would like the product section to look like a normal product section on Shopify, specified in the link below. The rest of the site with the featues and benefits and ingredients can be displayed creatively with images, illustrations, or product placement interspersed. Use any high quality images you have access to and we will purchase if necessary.

Use icons and symbols to represent the different benefits and ingredients.

Pay no attention to colors in the wireframe. The only defitinte color is the logo.

I put a picture of the actual suppositories so we would like to intersperse that (an individual one, not inside the package) in a few places. You can use it in the directions section for sure.

Video about wireframe: https://files.brovantic.net/file/d/9Kq2mRtzPw4LxVb7Hn3JcYd5FgS8aZeUo/view?usp=share

https://slides.brovantic.net/deck/d/7Tm3WqLpZx8NcRv2Bk6YhJs4DfG5aQeUi/edit?usp=share&uid=408213957260318846115&mode=true&full=true

Target Market(s)

Women

Industry/Entity Type

Healthcare

Number of Pages Required

1 page

Requirements
Must have
• I added a "wireframe" in the description
Nice to have
Should not have

```html
<!DOCTYPE html>
<html lang="en">
<head>
<meta charset="utf-8">
<title>Corlani Vaginal Suppositories</title>
<link rel="stylesheet" href="https://fonts.googleapis.com/css2?family=Manrope:wght@400;500;600;700&display=swap">
<style>
:root{
  --band:#f1b9bc;
  --ink:#2a2626;
  --muted:#7a7274;
  --brand:#e0267a;
  --hero-a:#f9e8e9;
  --hero-b:#f3d6d8;
  --panel:#f7f4f4;
  --line:#e6e0e1;
  --pink-card:#f5cfd0;
  --photo-a:#e2d6d9;
  --photo-b:#e8c2c5;
  --pill:#f1a9ae;
  --dark:#2b2a2a;
  --white:#ffffff;
}
*{box-sizing:border-box;margin:0;padding:0}
html,body{width:1200px;height:800px;overflow:hidden;background:var(--white)}
body{font-family:"Manrope",sans-serif;color:var(--ink);position:relative}
.promo-band{position:absolute;left:0;top:0;width:1200px;height:33px;background:var(--band);
  display:flex;align-items:center;justify-content:center;font-size:12px;font-weight:700;letter-spacing:.06em}
.promo-band .menu-lines{position:absolute;right:16px;top:12px}
.site-header{position:absolute;left:0;top:33px;width:1200px;height:62px;border-bottom:1px solid var(--line);background:var(--white)}
.brand{position:absolute;left:22px;top:17px;display:flex;align-items:center;gap:6px;font-size:26px;font-weight:700;color:var(--brand);letter-spacing:-.02em}
.brand-dot{width:10px;height:10px;border-radius:50%;background:var(--brand)}
.main-nav{position:absolute;left:385px;top:24px;display:flex;gap:38px;font-size:11px;font-weight:500;letter-spacing:.04em}
.search-field{position:absolute;left:1015px;top:15px;width:102px;height:29px;border:1px solid #d8d2d3;border-radius:15px;font-size:10px;padding:8px 16px;color:var(--muted)}
.header-icon{position:absolute;top:21px}
.hero{position:absolute;left:0;top:118px;width:805px;height:390px;border-radius:0 20px 20px 0;overflow:hidden;
  background:linear-gradient(100deg,var(--hero-a),var(--hero-b))}
.hero-title{position:absolute;left:57px;top:62px;font-size:58px;font-weight:500;line-height:1.1;letter-spacing:-.02em}
.hero-text{position:absolute;left:57px;top:212px;width:330px;font-size:16px;line-height:1.35;color:var(--muted)}
.hero-cta{position:absolute;left:56px;top:270px;width:162px;height:46px;border-radius:6px;background:var(--dark);color:var(--white);
  display:flex;align-items:center;justify-content:center;font-size:12px;font-weight:600;letter-spacing:.03em}
.hero-arrow{position:absolute;left:240px;top:286px}
.hero-photo{position:absolute;left:440px;top:20px;width:360px;height:370px;
  background:radial-gradient(ellipse 42% 48% at 50% 50%,#ffffff 0%,#fbe9ea 35%,#f0c9cc 62%,rgba(243,214,216,0) 100%)}
.side-panel{position:absolute;left:815px;top:118px;width:385px;height:390px;background:var(--panel);overflow:hidden}
.side-label{position:absolute;right:16px;top:18px;font-size:11px;font-weight:500;letter-spacing:.03em}
.side-foot{position:absolute;left:45px;bottom:10px;font-size:10px;font-weight:600;letter-spacing:.04em}
.ring{position:absolute;border-radius:50%;background:radial-gradient(circle,#f8dadc 0%,#f3cdd0 100%);display:flex;align-items:center;justify-content:center;z-index:2}
.ring span{width:46px;height:46px;border-radius:50%;background:radial-gradient(circle at 35% 35%,#f1b0b4,#d88a90);border:3px solid var(--white)}
.side-photo{position:absolute;left:60px;top:20px;width:290px;height:350px;
  background:radial-gradient(ellipse 36% 48% at 56% 50%,#ffffff 0%,#fbeff0 40%,#f2d6d8 65%,rgba(247,244,244,0) 100%)}
.card{position:absolute;top:520px;height:280px;border-radius:14px 14px 0 0;text-align:center;overflow:hidden}
.card-photo-one{left:0;width:296px;
  background:radial-gradient(ellipse 45% 55% at 45% 58%,#ffffff 0%,#f6dfe1 40%,#ead2d6 70%,var(--photo-a) 100%)}
.card-features{left:304px;width:292px;background:var(--pink-card)}
.card-photo-two{left:604px;width:292px;
  background:radial-gradient(ellipse 40% 52% at 50% 60%,#f7e3e4 0%,#dcb0b4 45%,#d9aeb2 70%,var(--photo-b) 100%)}
.card-trust{left:905px;width:295px;background:var(--panel)}
.pill{display:inline-block;padding:8px 18px;border-radius:16px;background:var(--pill);font-size:11px;font-weight:600;letter-spacing:.04em}
.card-features .pill{margin-top:28px}
.card-trust .pill{margin-top:45px;padding:7px 14px}
.card-heading{font-size:17px;font-weight:500;line-height:1.4;margin:16px 24px 0}
.card-text{font-size:14px;line-height:1.35;margin:18px 30px 0}
.stars{margin-top:30px;display:flex;justify-content:center;gap:10px}
.card-trust .card-heading{margin-top:18px}
.card-trust .card-text{margin-top:20px;font-size:14px}
.card-tag{margin-top:26px;font-size:20px;font-weight:600;letter-spacing:.02em}
</style>
</head>
<body>
<div class="promo-band">FREE SHIPPING ON ALL ORDERS OVER $40
  <svg class="menu-lines" width="22" height="10" viewBox="0 0 22 10"><path d="M0 1h22M4 5h18M0 9h22" stroke="#555" stroke-width="1.5"/></svg>
</div>

<header class="site-header">
  <div class="brand"><span class="brand-dot"></span>Corlani</div>
  <nav class="main-nav"><span>HOME</span><span>SHOP</span><span>ABOUT</span><span>INGREDIENTS</span><span>BENEFITS</span><span>CONTACT</span></nav>
  <div class="search-field">Search</div>
  <svg class="header-icon" style="left:1133px" width="18" height="18" viewBox="0 0 18 18"><circle cx="7.5" cy="7.5" r="5.5" fill="none" stroke="#333" stroke-width="1.6"/><path d="M11.5 11.5L16 16" stroke="#333" stroke-width="1.6"/></svg>
  <svg class="header-icon" style="left:1168px" width="20" height="18" viewBox="0 0 20 18"><path d="M1 2h3l2 10h10l2-7H5" fill="none" stroke="#333" stroke-width="1.6"/><circle cx="8" cy="15.5" r="1.5" fill="#333"/><circle cx="15" cy="15.5" r="1.5" fill="#333"/></svg>
</header>

<section class="hero">
  <div class="hero-photo" role="img" aria-label="Hand holding a white Corlani suppository jar with a pink label"></div>
  <h1 class="hero-title">Corlani vaginal<br>suppositories</h1>
  <p class="hero-text">We make the gentle moisture you deserve in an easy daily ritual.</p>
  <a class="hero-cta">SHOP NOW</a>
  <svg class="hero-arrow" width="88" height="16" viewBox="0 0 88 16"><path d="M0 8h86M78 1l8 7-8 7" fill="none" stroke="#222" stroke-width="1.5"/></svg>
</section>

<aside class="side-panel">
  <span class="side-label">DETAILS</span>
  <div class="side-photo" role="img" aria-label="Corlani vaginal suppositories jar with pink label"></div>
  <div class="ring" style="left:10px;top:95px;width:112px;height:112px"><span></span></div>
  <div class="ring" style="left:260px;top:220px;width:112px;height:112px"><span></span></div>
  <span class="side-foot">SHOP BENEFITS</span>
</aside>

<div class="card card-photo-one" role="img" aria-label="Hand holding a white Corlani suppository jar"></div>

<section class="card card-features">
  <span class="pill">FEATURES</span>
  <h2 class="card-heading">Features, Benefits &amp; Icons, Care and Easy Ingredients You'll Love</h2>
  <p class="card-text">Discover the soothing ritual for comfort every day.</p>
  <div class="stars">
    <svg width="130" height="16" viewBox="0 0 130 16" fill="#fff"><path id="st" d="M8 0l2.4 5 5.6.6-4.2 3.8 1.2 5.6L8 12.2 3 15l1.2-5.6L0 5.6 5.6 5z"/><use href="#st" x="24"/><use href="#st" x="48"/><use href="#st" x="72"/><use href="#st" x="96"/><circle cx="124" cy="8" r="5" fill="none" stroke="#fff" stroke-width="1.5"/></svg>
  </div>
</section>

<div class="card card-photo-two" role="img" aria-label="Hand holding an amber Corlani suppository jar"></div>

<section class="card card-trust">
  <span class="pill">TRUST</span>
  <h2 class="card-heading">Trusted by our loyal and caring customers</h2>
  <p class="card-text">Used by women seeking natural and lasting relief.</p>
  <div class="card-tag">REVIEWS</div>
</section>
</body>
</html>
```